Organization and people consulting firm needs a website design

I need a website that promotes and explains the consulting service we will provide. The organization is called Bluefinch Advisory Partners. Our services include organization design, employee experience, change management, and executive coaching. I would like to see a simple clean and professional design, that reflects a modern and forward looking professional services company

Target Market(s)

Mid market and large companies

Industry/Entity Type

Management Consulting

Coding

Coded - Design and coding required

Number of Pages Required

5+ page

Font styles to use
Sans Serif

Colors

Designer to choose colors to be used in the design.

Requirements
Must have
• The following pages: Home, The Way We Work, What We Do, Our Founder, Insights, Contact.
• Search button.
• Hyper links (will be provided with main body text)
• Scrolling website with summaries at top level and links to more detail at lower level (like this website: veltracore.com)
• Company logo (uploaded)
• I have text for each of the pages that I can upload once the basic design is done
Should not have
• No clutter, keep the design clean

```html
<!DOCTYPE html>
<html lang="en">
<head>
<meta charset="utf-8">
<title>Bluefinch Advisory Partners</title>
<link rel="stylesheet" href="https://fonts.googleapis.com/css2?family=Montserrat:wght@400;500;600;700&family=Open+Sans:wght@400;600;700&display=swap">
<style>
:root{
  --red:#e3173e;
  --ink:#1f1f1f;
  --body:#555555;
  --muted:#777777;
  --light:#f2f2f2;
  --white:#ffffff;
  --rule:#dddddd;
  --footer:#6b6b6b;
  --heading:'Montserrat', sans-serif;
  --text:'Open Sans', sans-serif;
}
*{margin:0;padding:0;box-sizing:border-box}
html,body{width:1200px;height:4036px;overflow:hidden}
body{position:relative;background:var(--white);font-family:var(--text);color:var(--body)}
section,footer,header{position:absolute;left:0;width:1200px}
.section-title{position:absolute;left:0;width:1200px;text-align:center;font-family:var(--heading);font-weight:400;font-size:32px;color:var(--ink)}
.btn{position:absolute;display:flex;align-items:center;justify-content:center;border:2px solid var(--red);color:var(--red);font-family:var(--heading);font-weight:600;font-size:13px;letter-spacing:.5px;text-transform:uppercase;text-decoration:none;background:transparent}

/* Hero */
.hero{top:0;height:657px}
.hero-photo{position:absolute;inset:0;background:linear-gradient(100deg,#e9e6e1 0%,#cfc7bd 28%,#9c8d80 52%,#5e5450 72%,#bdb3aa 100%)}
.logo{position:absolute;display:flex;align-items:center;gap:10px;font-family:var(--heading);font-weight:600;text-transform:uppercase;color:var(--red);letter-spacing:.3px;white-space:nowrap;font-size:14px}
.logo-mark{width:30px;height:30px;border-radius:50%;background:var(--red);flex:none}
.hero .logo{left:135px;top:40px}
.main-nav{position:absolute;top:16px;left:496px;display:flex;gap:4px;font-family:var(--heading);font-size:12.5px;font-weight:600;white-space:nowrap}
.main-nav a{color:var(--white);text-decoration:none;padding:6px 12px;border-radius:3px}
.main-nav a.active{background:var(--red)}
.hero-heading{position:absolute;left:147px;top:250px;font-family:var(--heading);font-weight:500;font-size:36px;line-height:44px;color:var(--ink)}
.hero-heading .accent{color:var(--red);font-weight:600}
.slide-arrow{position:absolute;top:304px;width:28px;height:34px;background:rgba(40,40,40,.75);display:flex;align-items:center;justify-content:center}
.slide-arrow.prev{left:0}
.slide-arrow.next{right:0}

/* Way we work */
.way{top:657px;height:438px}
.way .section-title{top:80px}
.way-text{position:absolute;left:340px;top:155px;width:520px;text-align:center;font-size:15px;line-height:23px;color:var(--body)}

/* What we do */
.services{top:1095px;height:715px;background:var(--light)}
.services .section-title{top:62px}
.service-card{position:absolute;width:404px;height:211px;background:var(--white);box-shadow:0 2px 8px rgba(0,0,0,.05)}
.service-icon{position:absolute;left:26px;top:44px;width:64px;height:64px}
.service-card h3{position:absolute;left:121px;top:42px;font-family:var(--heading);font-weight:500;font-size:17px;color:var(--ink)}
.service-card p{position:absolute;left:121px;top:78px;width:262px;font-size:12.5px;line-height:18px;color:var(--body)}

/* Founder */
.founder{top:1810px;height:650px}
.founder .section-title{top:105px}
.founder-photo{position:absolute;left:197px;top:237px;width:204px;height:204px;border-radius:50%;background:radial-gradient(circle at 50% 40%,#8a7f77,#3e3a3a 70%)}
.founder-name{position:absolute;left:150px;width:298px;top:470px;text-align:center;font-family:var(--heading);font-weight:700;font-size:15px;color:var(--ink)}
.founder-role{position:absolute;left:150px;width:298px;top:497px;text-align:center;font-size:14px;color:var(--muted)}
.founder-text{position:absolute;left:482px;width:540px;font-size:12.5px;line-height:18px;color:var(--body)}

/* Insights */
.insights{top:2460px;height:655px;background:var(--light)}
.insights .section-title{top:64px}
.insight{position:absolute;top:171px;width:269px}
.insight-photo{width:269px;height:191px}
.insight h3{margin-top:32px;font-family:var(--heading);font-weight:600;font-size:14px;color:var(--ink)}
.insight p{margin-top:10px;font-size:12.5px;line-height:17px;color:var(--body)}

/* Contact */
.contact{top:3115px;height:625px}
.contact .section-title{top:72px}
.contact-sub{position:absolute;left:0;width:1200px;top:126px;text-align:center;font-size:14px;color:var(--body)}
.contact-item{position:absolute;top:240px;width:250px;text-align:center}
.contact-icon{width:70px;height:70px;margin:0 auto;border-radius:50%;border:1px solid var(--rule);background:#fafafa;display:flex;align-items:center;justify-content:center}
.contact-item h4{margin-top:34px;font-family:var(--heading);font-weight:700;font-size:12px;letter-spacing:.5px;color:var(--ink)}
.contact-item p{margin-top:10px;font-size:12.5px;line-height:18px;color:var(--body)}
.contact-divider{position:absolute;top:234px;width:1px;height:162px;background:var(--rule)}

/* Footer */
.site-footer{top:3740px;height:296px;background:var(--footer)}
.site-footer .logo{left:135px;top:74px;color:var(--white)}
.site-footer .logo-mark{background:var(--white)}
.footer-divider{position:absolute;left:487px;top:48px;width:1px;height:80px;background:#9a9a9a}
.footer-nav{position:absolute;left:566px;top:83px;display:flex;font-family:var(--heading);font-weight:600;font-size:11px;color:var(--white);white-space:nowrap}
.footer-nav a{color:var(--white);text-decoration:none;padding:0 8px;border-left:1px solid #cfcfcf;line-height:12px}
.footer-nav a:first-child{border-left:none;padding-left:0}
.footer-rule{position:absolute;left:135px;top:182px;width:930px;height:1px;background:#7d7d7d}
.copyright{position:absolute;left:0;width:1200px;top:226px;text-align:center;font-family:var(--heading);font-weight:600;font-size:10.5px;color:var(--white);letter-spacing:.3px}
</style>
</head>
<body>

<header class="hero">
  <div class="hero-photo" role="img" aria-label="Photograph of two smiling consultants in suits reviewing a tablet at an office desk"></div>
  <div class="logo"><span class="logo-mark"></span>Bluefinch Advisory Partners</div>
  <nav class="main-nav">
    <a class="active" href="#">Home</a>
    <a href="#">The Way We Work</a>
    <a href="#">What We Do</a>
    <a href="#">Our Founder</a>
    <a href="#">Insights</a>
    <a href="#">Contact</a>
  </nav>
  <h1 class="hero-heading"><span class="accent">Organisation &amp;</span><br>People consulting firm</h1>
  <a class="slide-arrow prev" href="#" aria-label="Previous slide"><svg width="10" height="12" viewBox="0 0 10 12"><path d="M7 1 2 6l5 5" fill="none" stroke="#fff" stroke-width="2"/></svg></a>
  <a class="slide-arrow next" href="#" aria-label="Next slide"><svg width="10" height="12" viewBox="0 0 10 12"><path d="M3 1l5 5-5 5" fill="none" stroke="#fff" stroke-width="2"/></svg></a>
</header>

<section class="way">
  <h2 class="section-title">The Way We Work</h2>
  <p class="way-text">At vero eos et accusamus et iusto odio dignissimos ducimus qui blanditiis praesentium voluptatum deleniti atque corrupti quos dolores et quas molestias excepturi sint occaecati cupiditate non provident, similique sunt in culpa qui officia deserunt mollitia animi, id est laborum et dolorum fuga</p>
  <a class="btn" href="#" style="left:535px;top:295px;width:130px;height:46px">Learn More</a>
</section>

<section class="services">
  <h2 class="section-title">What We Do</h2>

  <article class="service-card" style="left:188px;top:164px">
    <svg class="service-icon" viewBox="0 0 64 64" fill="var(--red)">
      <circle cx="32" cy="12" r="6"/><path d="M23 30a9 9 0 0 1 18 0z"/>
      <circle cx="12" cy="40" r="6"/><path d="M3 58a9 9 0 0 1 18 0z"/>
      <circle cx="52" cy="40" r="6"/><path d="M43 58a9 9 0 0 1 18 0z"/>
      <path d="M32 31v8M32 39 18 44M32 39l14 5" stroke="var(--red)" stroke-width="2" fill="none"/>
    </svg>
    <h3>Organisation Design</h3>
    <p>At vero eos et accusamus et iusto odio dignissimos ducimus qui blanditiis praesentium voluptatum deleniti atque corrupti quos d olores et quas molestias excepturi sint occaecati cupiditate</p>
  </article>

  <article class="service-card" style="left:616px;top:164px">
    <svg class="service-icon" viewBox="0 0 64 64" fill="var(--red)">
      <path d="M10 6l2 4 4 .5-3 3 .8 4-3.8-2-3.8 2 .8-4-3-3 4-.5z"/>
      <path d="M32 2l2 4 4 .5-3 3 .8 4-3.8-2-3.8 2 .8-4-3-3 4-.5z"/>
      <path d="M54 6l2 4 4 .5-3 3 .8 4-3.8-2-3.8 2 .8-4-3-3 4-.5z"/>
      <circle cx="32" cy="30" r="9"/><path d="M16 62c0-12 7-19 16-19s16 7 16 19z"/>
    </svg>
    <h3>Employee Experience</h3>
    <p>At vero eos et accusamus et iusto odio dignissimos ducimus qui blanditiis praesentium voluptatum deleniti atque corrupti quos d olores et quas molestias excepturi sint occaecati cupiditate</p>
  </article>

  <article class="service-card" style="left:188px;top:401px">
    <svg class="service-icon" viewBox="0 0 64 64">
      <circle cx="32" cy="32" r="22" fill="none" stroke="var(--red)" stroke-width="8" stroke-dasharray="7 4.5"/>
      <circle cx="32" cy="32" r="17" fill="var(--red)"/>
      <circle cx="32" cy="27" r="5" fill="#fff"/><path d="M23 42a9 9 0 0 1 18 0z" fill="#fff"/>
    </svg>
    <h3>Change Management</h3>
    <p>At vero eos et accusamus et iusto odio dignissimos ducimus qui blanditiis praesentium voluptatum deleniti atque corrupti quos d olores et quas molestias excepturi sint occaecati cupiditate</p>
  </article>

  <article class="service-card" style="left:616px;top:401px">
    <svg class="service-icon" viewBox="0 0 64 64" fill="var(--red)">
      <circle cx="32" cy="16" r="11"/><path d="M14 62c0-18 8-28 18-28s18 10 18 28z"/>
    </svg>
    <h3>Executive coaching</h3>
    <p>At vero eos et accusamus et iusto odio dignissimos ducimus qui blanditiis praesentium voluptatum deleniti atque corrupti quos d olores et quas molestias excepturi sint occaecati cupiditate</p>
  </article>
</section>

<section class="founder">
  <h2 class="section-title">Our Founder</h2>
  <div class="founder-photo" role="img" aria-label="Portrait photograph of the founder in a grey suit"></div>
  <div class="founder-name">Daniel Marsh</div>
  <div class="founder-role">Founder</div>
  <p class="founder-text" style="top:236px">Nam libero tempore, cum soluta nobis est eligendi optio cumque nihil impedit quo minus id quod maxime placeat facere possimus, omnis voluptas assumenda est, omnis dolor repellendus. Temporibus autem</p>
  <p class="founder-text" style="top:322px">At vero eos et accusamus et iusto odio dignissimos ducimus qui blanditiis praesentium voluptatum deleniti atque corrupti quos dolores et quas molestias excepturi sint occaecati cupiditate non provident, similique sunt in culpa qui officia deserunt mollitia animi, id est laborum et dolorum fuga. Et harum quidem rerum facilis est et expedita distinctio. Nam libero tempore, cum soluta nobis est eligendi optio cumque nihil impedit quo minus id quod maxime placeat facere possimus, omnis voluptas assumenda est, omnis dolor repellendus. Temporibus autem</p>
  <a class="btn" href="#" style="left:482px;top:477px;width:185px;height:44px">More About Daniel</a>
</section>

<section class="insights">
  <h2 class="section-title">Insights</h2>
  <article class="insight" style="left:151px">
    <div class="insight-photo" role="img" aria-label="Photograph of a smiling businessman at a desk in a bright office" style="background:linear-gradient(120deg,#f1dcc0,#c79a6a 55%,#e9d6c0)"></div>
    <h3>At vero eos et accusamus</h3>
    <p>Nam libero tempore, cum soluta nobis est eligendi optio cumque nihil impedit quo minus id quod maxime placeat facere.</p>
  </article>
  <article class="insight" style="left:465px">
    <div class="insight-photo" role="img" aria-label="Photograph of hands signing a document on a wooden desk" style="background:linear-gradient(120deg,#2b2b2d,#6e5a48 50%,#c4a27c)"></div>
    <h3>At vero eos et accusamus</h3>
    <p>Nam libero tempore, cum soluta nobis est eligendi optio cumque nihil impedit quo minus id quod maxime placeat facere.</p>
  </article>
  <article class="insight" style="left:785px">
    <div class="insight-photo" role="img" aria-label="Photograph of charts and reports spread on a meeting table" style="background:linear-gradient(120deg,#eef1f3,#b8c8d6 55%,#dfe6ec)"></div>
    <h3>At vero eos et accusamus</h3>
    <p>Nam libero tempore, cum soluta nobis est eligendi optio cumque nihil impedit quo minus id quod maxime placeat facere.</p>
  </article>
  <a class="btn" href="#" style="left:518px;top:545px;width:166px;height:44px">View All Insights</a>
</section>

<section class="contact">
  <h2 class="section-title">Contact Bluefinch</h2>
  <p class="contact-sub">Nam libero tempore, cum soluta nobis est eligendi o cumque</p>

  <div class="contact-item" style="left:195px">
    <div class="contact-icon"><svg width="16" height="22" viewBox="0 0 16 22"><path d="M8 0a8 8 0 0 0-8 8c0 6 8 14 8 14s8-8 8-14a8 8 0 0 0-8-8zm0 11a3 3 0 1 1 0-6 3 3 0 0 1 0 6z" fill="#555"/></svg></div>
    <h4>ADDRESS</h4>
    <p>1180 Harlow Street, Marden,<br>OR 97120</p>
  </div>
  <div class="contact-divider" style="left:471px"></div>
  <div class="contact-item" style="left:475px">
    <div class="contact-icon"><svg width="20" height="20" viewBox="0 0 24 24"><path d="M6.6 10.8a15 15 0 0 0 6.6 6.6l2.2-2.2c.3-.3.7-.4 1-.2 1.1.4 2.3.6 3.6.6.6 0 1 .4 1 1V20c0 .6-.4 1-1 1A17 17 0 0 1 3 4c0-.6.4-1 1-1h3.5c.6 0 1 .4 1 1 0 1.3.2 2.5.6 3.6.1.3 0 .7-.2 1z" fill="#555"/></svg></div>
    <h4>CALL US</h4>
    <p>555 014 2870</p>
  </div>
  <div class="contact-divider" style="left:721px"></div>
  <div class="contact-item" style="left:757px">
    <div class="contact-icon"><svg width="20" height="16" viewBox="0 0 20 16"><rect width="20" height="16" rx="2" fill="#555"/><path d="M1 2l9 7 9-7" fill="none" stroke="#fafafa" stroke-width="1.6"/></svg></div>
    <h4>E MAIL US</h4>
    <p>hello@bluefinchadvisory.com</p>
  </div>

  <a class="btn" href="#" style="left:533px;top:482px;width:132px;height:44px">Get In Touch</a>
</section>

<footer class="site-footer">
  <div class="logo"><span class="logo-mark"></span>Bluefinch Advisory Partners</div>
  <div class="footer-divider"></div>
  <nav class="footer-nav">
    <a href="#">HOME</a><a href="#">THE WAY WE WORK</a><a href="#">WHAT WE DO</a><a href="#">OUR FOUNDER</a><a href="#">INSIGHTS</a><a href="#">CONTACT</a>
  </nav>
  <div class="footer-rule"></div>
  <p class="copyright">COPYRIGHTS @ 2016 ALL RIGHTS RESERVED</p>
</footer>

</body>
</html>
```